Zelvo Stationary

Design the stationary of Zelvo Promotions Group.

Zelvo is a BTL company, BTL meaning "below the line". In other words Zelvo is a Promotional Marketing company (the company that design the brands promotional activities).

The design should transmit creativity, agility, boldness.

I need:
* Bis Card
* Letter head
* Envelopes, both vertical and horizontal (for legal size), and letter envelope
* Folders
* PPT template (Title page and regular page)
* CD slip (CD envelope)
* ID card (employee card)

And what ever else you want to throw in.
Updates

Guys,

Something I missed from the brief.   The predominat color should be RED.

Also, have fun and play with the exclamation mark (!) of the logo. 

Hi guys, more comments:

Remember that Zelvo is a "creativity" agency, not in the advertising side but on the promotional side, and that should reflect on the stationary.

 I want a bold design.  Bold and yet crisp.

 

Guys, i just uploaded the Logo in AI format.

I Also uploaded the actual Zelvo Bis Card, wich I like.  So I will like to see some designs with that bis card approach.

Guys, I am so sorry, but I notice in your last post that I upladed a wrong design ("13154_promotions_group_zelvo_brief225630.ai").  The problem was that I asked the designer the file in AI format and he send me thw wrong file, and since I dont have Illustrator I could not verify it.

The differences are minor, I just already ask him the correct one (similar to the EPS file).

Sorry                                   

Just post the correct AI file : "Zelvo Logo.ai"

Reason: I'm expecting more designs to choose from and also I wont be available tomorrow to decide.

Reason: Sorry guys, but we are not there yet!

Target Market(s)

Marketing directors, Marketing Managers

Industry/Entity Type

Legal

Requirements
Must have
• Must work with the logo attached.
The predominat color should be RED.
Play and have fun with the exclamation mark (!).
Should not have
• * No old fonts

Should not be:
* boring
* Informal
* rigid

```html
<!DOCTYPE html>
<html lang="es">
<head>
<meta charset="utf-8">
<title>Zelvo Promotions Group — Letterhead</title>
<link href="https://fonts.googleapis.com/css2?family=Montserrat:wght@500;700&display=swap" rel="stylesheet">
<style>
  :root {
    --red: #d3121b;
    --red-deep: #a80b12;
    --red-dark: #7e070c;
    --red-light: #e4323a;
    --paper: #ffffff;
    --ink-light: #ffffff;
  }
  html, body {
    margin: 0;
    padding: 0;
    overflow: hidden;
    background: var(--paper);
  }
  .letterhead {
    position: relative;
    width: 849px;
    height: 1200px;
    background: var(--paper);
    overflow: hidden;
    font-family: "Montserrat", Arial, sans-serif;
  }
  .letterhead svg {
    position: absolute;
    left: 0;
    top: 0;
  }
  .brand-name {
    font-family: "Montserrat", Arial, sans-serif;
    font-weight: 700;
    font-size: 64px;
    fill: var(--ink-light);
  }
  .brand-tagline {
    font-family: "Montserrat", Arial, sans-serif;
    font-weight: 500;
    font-size: 19px;
    letter-spacing: 2px;
    fill: var(--ink-light);
  }
  .contact-block {
    position: absolute;
    left: 652px;
    top: 1008px;
    width: 190px;
    color: var(--ink-light);
    font-size: 10.5px;
    font-weight: 700;
    font-style: normal;
    line-height: 1.85;
    white-space: nowrap;
    margin: 0;
  }
  .contact-web {
    position: absolute;
    left: 652px;
    top: 1130px;
    color: var(--ink-light);
    font-size: 16.5px;
    font-weight: 700;
    white-space: nowrap;
    margin: 0;
  }
</style>
</head>
<body>
<main class="letterhead">
  <svg width="849" height="1200" viewBox="0 0 849 1200">
    <polygon class="header-band" points="0,0 849,0 849,50 170,156 0,113" fill="var(--red)"/>
    <polygon class="header-shade" points="0,0 849,0 849,22 300,80 0,60" fill="var(--red-deep)" opacity="0.55"/>
    <polygon class="header-strip" points="0,113 170,156 849,50 849,88 170,202 0,160" fill="var(--red-light)"/>
    <polygon class="header-edge" points="0,160 170,202 849,88 849,96 170,212 0,170" fill="var(--red-deep)"/>

    <text class="brand-name" x="98" y="98">zelvo</text>
    <circle class="brand-dot" cx="300" cy="80" r="14" fill="var(--ink-light)"/>
    <text class="brand-tagline" x="198" y="183" transform="rotate(-9 198 183)">PROMOTIONS GROUP</text>

    <polygon class="corner-block" points="628,935 849,890 849,1200 628,1200" fill="var(--red)"/>
    <polygon class="corner-shade" points="628,935 849,890 849,990" fill="var(--red-dark)"/>
    <polygon class="corner-fold" points="628,935 849,990 849,1010 628,965" fill="var(--red-deep)" opacity="0.6"/>
  </svg>

  <address class="contact-block">
    Calle 12 No. 48 Ens La Paz<br>
    Santo Domingo,<br>
    Republica Dominicana<br>
    Tell: 809.555.0142<br>
    Fax: 809.555.0187
  </address>
  <p class="contact-web">www.zelvo.com.do</p>
</main>
</body>
</html>
```